Every Shelf Set Neatly or ESN Organized needs a business card design. ESN Organized is a professi

We need a business card design that is clean, sharp and conveys a sense of organization. I already have a logo.

Target Market(s)

Families (specifically mothers), small business owners, parents, seniors

Industry/Entity Type

Business

Contact Information for Business Card

My website is www.esnorganized-example.com and my Facebook page is http://www.sociallink-example.com/everyshelfsetneatly. The phone number is 418-552-7094 and I want to be listed as Lorna M. Pelham, Owner

Requirements
Must have
• My logo.

```html
<!DOCTYPE html>
<html lang="en">
<head>
<meta charset="utf-8">
<title>Every Shelf Set Neatly – Business Card</title>
<link rel="stylesheet" href="https://fonts.googleapis.com/css2?family=Lato:wght@400;900&display=swap">
<style>
  :root {
    --backdrop: #2a2a2a;
    --card: #f3f3f3;
    --ink: #2b2b2b;
    --brand-blue: #1a6fc4;
    --band-black: #0d0d0d;
  }
  * { margin: 0; padding: 0; box-sizing: border-box; }
  html, body {
    width: 1200px; height: 873px; overflow: hidden;
    background: var(--backdrop);
    font-family: "Lato", sans-serif;
  }
  .stage {
    width: 1200px; height: 873px;
    display: flex; align-items: center; justify-content: center;
  }
  .business-card {
    position: relative;
    width: 840px; height: 480px;
    background: var(--card);
    overflow: hidden;
    box-shadow: 0 12px 40px rgba(0,0,0,.45);
  }
  .brand {
    position: absolute; left: 70px; top: 84px;
  }
  .brand-name {
    font-size: 40px; font-weight: 400;
    color: var(--ink);
  }
  .owner {
    position: absolute; right: 80px; top: 196px;
    text-align: right;
  }
  .owner-name {
    font-size: 28px; font-weight: 900; color: var(--brand-blue);
  }
  .owner-title {
    font-size: 20px; font-weight: 400; color: var(--ink); margin-top: 4px;
  }
  .contact-list {
    position: absolute; left: 70px; top: 296px;
    list-style: none;
  }
  .contact-item {
    display: flex; align-items: center; gap: 14px;
    font-size: 24px; color: var(--ink);
    margin-bottom: 18px;
  }
  .contact-icon {
    width: 32px; height: 32px; flex: none;
  }
  .band-black {
    position: absolute; left: 0; right: 0; bottom: 40px; height: 14px;
    background: var(--band-black);
  }
  .band-blue {
    position: absolute; left: 0; right: 0; bottom: 0; height: 34px;
    background: var(--brand-blue);
  }
</style>
</head>
<body>
<main class="stage">
  <article class="business-card">
    <header class="brand">
      <span class="brand-name">Every Shelf Set Neatly</span>
    </header>

    <div class="owner">
      <p class="owner-name">Lorna M. Pelham</p>
      <p class="owner-title">Owner</p>
    </div>

    <ul class="contact-list">
      <li class="contact-item">
        <svg class="contact-icon" viewBox="0 0 30 30" aria-hidden="true">
          <circle cx="15" cy="15" r="15" fill="#1a6fc4"/>
          <path d="M9 12c0-2 2-3.5 6-3.5s6 1.5 6 3.5l-2.5 .8-.6-1.8h-5.8l-.6 1.8z" fill="#fff"/>
          <rect x="9.5" y="14" width="11" height="7" rx="1.5" fill="#fff"/>
          <circle cx="15" cy="17.5" r="2" fill="#1a6fc4"/>
        </svg>
        <span>418-552-7094</span>
      </li>
      <li class="contact-item">
        <svg class="contact-icon" viewBox="0 0 30 30" aria-hidden="true">
          <circle cx="15" cy="15" r="15" fill="#1a6fc4"/>
        </svg>
        <span>sociallink-example.com/everyshelfsetneatly</span>
      </li>
    </ul>

    <div class="band-black"></div>
    <div class="band-blue"></div>
  </article>
</main>
</body>
</html>
```